Maine Organic farm needs a label design for various food products

We need a label design that we can use across a variety of vegetable-based food products that we produce using some of our organic vegetables that we grow on our farm located in Maine, USA.
Our products include:
1) a Traditional and Vegan Korean Kimchi
2) Sumel Sauce (a Korean Hot Sauce)
3) Pickles of Brambleton Relish
4) Brinjalista Chutney
5) Seasonal Soups (many varieties, depending on what's available during the season)
6) Firm Ranks Maple Syrup (we are retired from the Coastal Lancer Guard, hence the name and spelling)
7) Maine Wild Blueberry Kombucha (made with organic Maine wild blueberries)

For the Korean products (kimchi and Sumel Sauce) we would like to incorporate the Korean chili pepper (red) and chopsticks. The attached picture was taken from the internet, it has not been trademarked, but I am hesitant to use it as is as our business expands. Would like the "kimchi" to somehow incorporate the chopstick and pepper, but not look exactly like the attached image.

The final design should communicate farm fresh, organic, healthy and high quality ingredients, and Maine-made. All of our products go into glass jars 16oz and 8 oz. The hot sauce goes into 5.5oz and 8 oz bottles, the Maple Syrup goes into 8oz and 16oz bottles, and a 12oz bottle for the Kombucha. We will need the flexibility of changing some components of the label to accommodate each different food product.

The labels do not have the encircle the entirety of the jar. We understand that this is a tall order to fit so many different products. We are hoping that once we get the feel and design down, we can work with you for a fee outside of the competition to finalize other products labels on different sizes jars, bottles, etc. Its most important that we get the right feel for a label that can be used for a wide variety of food products.

Target Market(s)

Health conscious, foodies, local farm supporters

Font styles to use
Serif
Decorative
Script

Colors

Designer to choose colors to be used in the design.

Requirements
Must have
• Wendle Brook Farm Logo. Room for product name (interchangeable per product), ingredients list, space for jar size (8 oz, 12 oz, 16 oz). On Korean products -must have Korean hot chili pepper and chopsticks
Nice to have
• We'd like something fairly bold and rustic looking.
Should not have
• Nothing too modern or industrial looking. Nothing hippy-ish. Clean and professional. No cartoonish looking letters or designs.

```html
<!DOCTYPE html>
<html lang="en">
<head>
<meta charset="utf-8">
<title>Wendle Brook Farm Labels</title>
<link rel="stylesheet" href="https://fonts.googleapis.com/css2?family=Arimo:wght@400;700&family=Tinos:ital,wght@0,700;1,400;1,700&display=swap">
<style>
  :root {
    --backdrop: #f2f2f2;
    --label-top: #ffffff;
    --label-bottom: #eaeaea;
    --frame: #6d6d6d;
    --ink: #111111;
    --brand-navy: #1d3352;
    --chili-red: #c8141b;
    --sketch-tone: #e4dfd6;
    --chopstick: #8a5a33;
    --tomato: #d4452a;
  }
  * { box-sizing: border-box; margin: 0; padding: 0; }
  html, body { width: 1053px; height: 1200px; overflow: hidden; }
  body { background: var(--backdrop); position: relative; font-family: "Tinos", serif; color: var(--ink); }

  .label {
    position: absolute;
    background: linear-gradient(180deg, var(--label-top) 0%, var(--label-bottom) 100%);
    box-shadow: 0 2px 10px rgba(0,0,0,0.12);
  }
  .label--syrup { left: 50px; top: 362px; width: 540px; height: 476px; }
  .label--sauce { left: 650px; top: 382px; width: 330px; height: 440px; }

  .frame-outer, .frame-inner { position: absolute; border: 1px solid var(--frame); pointer-events: none; }
  .frame-outer { inset: 6px; }
  .frame-inner { inset: 11px; border-color: #9a9a9a; }

  .farm-scene {
    position: absolute; left: 14px; right: 14px; top: 14px;
    background: linear-gradient(180deg, rgba(228,223,214,0) 0%, var(--sketch-tone) 60%, rgba(228,223,214,0.2) 100%);
  }
  .label--syrup .farm-scene { height: 120px; }
  .label--sauce .farm-scene { height: 100px; }

  .farm-brand {
    position: absolute; display: flex; align-items: center; gap: 6px;
    font-family: "Arimo", sans-serif; font-weight: 700; color: var(--brand-navy);
    white-space: nowrap;
  }
  .farm-brand .brand-dot { border-radius: 50%; background: var(--brand-navy); flex: none; }
  .label--syrup .farm-brand { left: 0; right: 0; justify-content: center; top: 96px; font-size: 21px; }
  .label--syrup .brand-dot { width: 14px; height: 14px; }
  .label--sauce .farm-brand { left: 40px; top: 90px; font-size: 14px; }
  .label--sauce .brand-dot { width: 10px; height: 10px; }

  .product-name {
    position: absolute; left: 0; right: 0; text-align: center;
    font-family: "Arimo", sans-serif; font-weight: 700; text-transform: uppercase; line-height: 1;
  }
  .label--syrup .product-name { top: 188px; font-size: 62px; letter-spacing: -1px; }
  .label--sauce .product-name { top: 180px; font-size: 38px; left: -30px; }

  .product-type {
    position: absolute; left: 0; right: 0; text-align: center;
    font-family: "Arimo", sans-serif; font-weight: 700; font-variant: small-caps; line-height: 1;
  }
  .label--syrup .product-type { top: 252px; font-size: 36px; color: var(--chili-red); }
  .label--sauce .product-type { top: 224px; font-size: 26px; color: var(--ink); }
  .product-type .accent { color: var(--chili-red); }

  .korean-motif {
    position: absolute; left: 224px; top: 68px; width: 78px; height: 150px;
    background: linear-gradient(160deg, var(--chopstick) 0%, #b07a4c 50%, var(--chili-red) 100%);
    opacity: 0.85; border-radius: 6px;
  }

  .ingredients {
    position: absolute; border-top: 1px solid var(--frame); border-bottom: 1px solid var(--frame);
    font-style: italic; font-weight: 700; text-align: center; line-height: 1.22;
    display: flex; align-items: center; justify-content: center;
  }
  .ingredients::before, .ingredients::after {
    content: ""; position: absolute; top: 0; bottom: 0; width: 1px; background: var(--frame);
  }
  .ingredients::before { left: 10px; } .ingredients::after { right: 10px; }
  .label--syrup .ingredients { left: 14px; right: 14px; top: 322px; height: 90px; font-size: 15px; padding: 0 30px; }
  .label--sauce .ingredients { left: 14px; right: 14px; top: 282px; height: 88px; font-size: 14px; padding: 0 22px; }

  .storage-row { position: absolute; display: flex; justify-content: space-between; align-items: baseline; }
  .storage-row .storage { font-style: italic; font-size: 11px; font-weight: 700; }
  .storage-row .volume { font-weight: 700; font-size: 18px; }
  .label--syrup .storage-row { left: 40px; right: 54px; top: 424px; }
  .label--sauce .storage-row { left: 36px; right: 70px; top: 384px; }
  .label--sauce .storage-row .storage { font-weight: 400; }
  .label--sauce .storage-row .volume { font-weight: 400; font-size: 15px; }

  .address {
    position: absolute; left: 14px; right: 14px; display: flex; align-items: center; gap: 8px;
    font-weight: 700; letter-spacing: 1px; white-space: nowrap;
  }
  .address::before, .address::after { content: ""; flex: 1; height: 1px; background: var(--frame); }
  .label--syrup .address { top: 452px; font-size: 15px; }
  .label--sauce .address { top: 412px; font-size: 13px; letter-spacing: 0.5px; }

  .tomato-accent {
    position: absolute; right: 8px; top: 368px; width: 40px; height: 40px; border-radius: 50%;
    background: radial-gradient(circle at 40% 40%, #e86a4c, var(--tomato));
  }
</style>
</head>
<body>

<section class="label label--syrup">
  <div class="frame-outer"></div>
  <div class="frame-inner"></div>
  <div class="farm-scene" role="img" aria-label="Faint line sketch of farm fields and barns"></div>
  <div class="farm-brand"><span class="brand-dot"></span>WENDLE BROOK FARM</div>
  <h1 class="product-name">Firm Ranks</h1>
  <p class="product-type">Maple Syrup</p>
  <div class="ingredients">ingredients: Lorem Ipsum, Proin gravida, nibh vel velit, auctor aliquet. Aenean sollicitudin, lorem quis bibendum auctor, nisi elit consequat ipsum, nec sagittis</div>
  <div class="storage-row"><span class="storage">Refrigerate after opening</span><span class="volume">16 fl oz</span></div>
  <div class="address">418, Larkin Rd, Aldwater ME,04000</div>
</section>

<section class="label label--sauce">
  <div class="frame-outer"></div>
  <div class="frame-inner"></div>
  <div class="farm-scene" role="img" aria-label="Faint line sketch of farm fields and hills"></div>
  <div class="farm-brand"><span class="brand-dot"></span>WENDLE BROOK FARM</div>
  <div class="korean-motif" role="img" aria-label="Crossed wooden chopsticks with a red Korean chili pepper"></div>
  <h1 class="product-name">Sumel</h1>
  <p class="product-type">Korean <span class="accent">Hot</span> Sauce</p>
  <div class="ingredients">ingredients: Lorem Ipsum, Proin gravida, nibh vel velit, auctor aliquet. Aenean sollicitudin, lorem quis bibendum auctor, nisi elit</div>
  <div class="storage-row"><span class="storage">Keep Refrigerated</span><span class="volume">5.5oz</span></div>
  <div class="tomato-accent" role="img" aria-label="Small ripe red tomato"></div>
  <div class="address">418, Larkin Rd, Aldwater ME,04000</div>
</section>

</body>
</html>
```